Ward Compass Business Card Design*

We need a business card design for our company Ward Compass. Our company is specialized in providing online consulting services regarding medical institutions, hospitals and doctors. We work with patients worldwide looking to choose between healthcare providers. We have a website you may use as a reference, where we list doctors and clinics worldwide. So we target Medical providers as well as patients worldwide.
Target Market(s)
Medical Providers and patients around the world
Industry/Entity Type
Medical
Contact Information for Business Card
Salwa Kettani
CEO
+90 612 348 2175
info@wardcompass.example
www.wardcompass.example
14 Annakhil 7 H.R.B. Rabat, Morocco
Requirements
Must have
- Company logo/name on one full side, personal info and smaller logo and company name on the other side.
Nice to have
- Smart and elegant design

```html
<!DOCTYPE html>
<html lang="en">
<head>
<meta charset="utf-8">
<title>Ward Compass – Business Card</title>
<link href="https://fonts.googleapis.com/css2?family=Montserrat:wght@400;600;700&display=swap" rel="stylesheet">
<style>
  :root {
    --navy: #12406a;
    --ink: #4a4a4a;
    --rule: #8a8a8a;
    --paper: #ffffff;
    --backdrop: #e4e6e9;
    --muted: #7d8ea3;
  }
  * { box-sizing: border-box; margin: 0; padding: 0; }
  html, body {
    width: 1200px; height: 800px; overflow: hidden;
    background: var(--backdrop);
    font-family: "Montserrat", Arial, sans-serif;
  }
  .sheet {
    position: relative; width: 1200px; height: 800px;
    display: flex; flex-direction: column; align-items: center;
    justify-content: center; gap: 40px;
  }
  .card {
    position: relative; width: 600px; height: 340px;
    box-shadow: 0 6px 18px rgba(0,0,0,.18);
  }
  .card--brand { background: var(--navy); }
  .card--contact { background: var(--paper); }

  .wordmark {
    display: flex; align-items: center; gap: 14px;
    font-weight: 600; letter-spacing: .06em; text-transform: uppercase;
    white-space: nowrap;
  }
  .wordmark__dot { width: 34px; height: 34px; border-radius: 50%; flex: none; }

  .card--brand .wordmark {
    position: absolute; left: 60px; bottom: 90px;
    font-size: 26px; color: var(--paper);
  }
  .card--brand .wordmark__dot { background: var(--paper); }

  .card--contact .wordmark {
    position: absolute; left: 42px; top: 142px;
    font-size: 22px; color: var(--navy);
  }
  .card--contact .wordmark__dot { background: var(--navy); width: 30px; height: 30px; }

  .divider {
    position: absolute; left: 326px; top: 80px; width: 1px; height: 180px;
    background: var(--rule);
  }
  .details {
    position: absolute; left: 352px; top: 92px;
    color: var(--ink); font-size: 14px; line-height: 1.45;
  }
  .details__name { color: var(--navy); font-weight: 700; font-size: 19px; line-height: 1.1; }
  .details__role { font-size: 14px; margin-bottom: 12px; }
  .details__address { margin-bottom: 2px; }
  .details__line { display: flex; align-items: center; gap: 8px; }
  .details__line svg { width: 13px; height: 13px; flex: none; fill: none; stroke: var(--navy); stroke-width: 1.6; }
  .details__line .icon-solid { fill: var(--navy); stroke: none; }
</style>
</head>
<body>
<main class="sheet">
  <section class="card card--brand" aria-label="Card front">
    <div class="wordmark"><span class="wordmark__dot"></span>Ward Compass</div>
  </section>

  <section class="card card--contact" aria-label="Card back">
    <div class="wordmark"><span class="wordmark__dot"></span>Ward Compass</div>
    <div class="divider"></div>
    <div class="details">
      <p class="details__name">Salwa Kettani</p>
      <p class="details__role">CEO</p>
      <p class="details__address">14 Annakhil 7<br>H.R.B. Rabat, Morocco</p>
      <p class="details__line">
        <svg viewBox="0 0 16 16"><path class="icon-solid" d="M3.5 1l3 3-1.6 2a9 9 0 0 0 5 5l2-1.6 3 3-2 2.4C6.5 14.6 1.4 9.5 1.2 3z"/></svg>
        +90 612 348 2175
      </p>
      <p class="details__line">
        <svg viewBox="0 0 16 16"><rect x="1.5" y="3.5" width="13" height="9"/><path d="M1.5 3.5l6.5 5 6.5-5"/></svg>
        info@wardcompass.example
      </p>
      <p class="details__line">
        <svg viewBox="0 0 16 16"><circle cx="8" cy="8" r="6.5"/><ellipse cx="8" cy="8" rx="3" ry="6.5"/><path d="M1.5 8h13"/></svg>
        www.wardcompass.example
      </p>
    </div>
  </section>
</main>
</body>
</html>
```